Business Card for Fashion House

We need a business card design for our personalize fashion service for our customers. the business card should reflect reliability, luxury and creativity.
The brand Gravetto is extracted from "Graceful Velvetto"; Gravetto provides fashion designs sprinkled with luxury and style tailored for our elite clients character profile.
Gravetto is created for those who embody class and elegance with a passion for style.
Target Market(s)
Affluent Customers
Industry/Entity Type
Fashion
Contact Information for Business Card
Samira Haddadin
Fashion Designer
Telephone: +971 4 555 0192
Mobile +971 50 555 0147
Emal info@gravetto-example.com
Website www.gravetto-example.com
Social Media Youtube g+ Facebook Instagram Pin /gravetto
Font styles to use
Other font styles liked:
- Audrey provided
Look and feel
Each slider illustrates characteristics of the customer's brand and the style your logo design should communicate.

```html
<!DOCTYPE html>
<html lang="en">
<head>
<meta charset="utf-8">
<title>Gravetto — Business Card</title>
<link rel="stylesheet" href="https://fonts.googleapis.com/css2?family=Marcellus&family=Lato:wght@400;700&family=Cormorant+Garamond:ital,wght@0,500;1,500&display=swap">
<style>
  :root {
    --stage: #e8e6e3;
    --card: #3a3231;
    --ink: #f3f1ee;
    --ink-soft: #c9c3bf;
    --rule: #8d8581;
  }
  * { box-sizing: border-box; margin: 0; padding: 0; }
  html, body { width: 1200px; height: 1000px; overflow: hidden; }
  body { background: var(--stage); position: relative; font-family: "Lato", sans-serif; }

  .card {
    position: absolute;
    width: 620px; height: 354px;
    background: var(--card);
    border-radius: 22px;
    box-shadow: 0 14px 34px rgba(0,0,0,.22);
    color: var(--ink);
  }
  .card--front { left: 70px; top: 80px; }
  .card--back  { left: 510px; top: 540px; }

  .brand-mark {
    display: block;
    width: 64px; height: 64px;
    border: 3px solid var(--ink);
    border-radius: 50%;
  }
  .wordmark {
    font-family: "Marcellus", serif;
    font-weight: 400;
    letter-spacing: .42em;
    color: var(--ink);
  }

  /* Front */
  .card--front .brand-mark { position: absolute; left: 278px; top: 62px; }
  .card--front .wordmark { position: absolute; left: 0; right: 0; top: 160px; text-align: center; font-size: 40px; padding-left: .42em; }
  .social { position: absolute; left: 0; right: 0; top: 262px; display: flex; justify-content: center; align-items: center; gap: 12px; }
  .social__dot { width: 16px; height: 16px; border-radius: 50%; background: var(--ink); }
  .social__handle { font-family: "Cormorant Garamond", serif; font-size: 19px; margin-left: 6px; }

  /* Back */
  .card--back .brand-mark { position: absolute; left: 310px; top: 42px; width: 54px; height: 54px; }
  .card--back .wordmark { position: absolute; left: 170px; top: 116px; font-size: 32px; }
  .person { position: absolute; left: 48px; top: 248px; }
  .person__name { font-weight: 700; font-size: 25px; letter-spacing: .01em; text-transform: uppercase; }
  .person__role { font-family: "Cormorant Garamond", serif; font-size: 18px; color: var(--ink-soft); margin-left: 70px; }
  .divider { position: absolute; left: 330px; top: 188px; width: 1px; height: 118px; background: var(--rule); }
  .contact { position: absolute; left: 348px; top: 190px; list-style: none; }
  .contact li { display: flex; align-items: center; gap: 10px; font-family: "Cormorant Garamond", serif; font-size: 17px; line-height: 28px; }
  .contact svg { width: 14px; height: 14px; flex: none; fill: var(--ink); }
</style>
</head>
<body>

<section class="card card--front" aria-label="Card front">
  <span class="brand-mark" aria-hidden="true"></span>
  <h1 class="wordmark">GRAVETTO</h1>
  <div class="social">
    <span class="social__dot"></span>
    <span class="social__dot"></span>
    <span class="social__dot"></span>
    <span class="social__dot"></span>
    <span class="social__dot"></span>
    <span class="social__handle">/gravetto</span>
  </div>
</section>

<section class="card card--back" aria-label="Card back">
  <span class="brand-mark" aria-hidden="true"></span>
  <p class="wordmark">GRAVETTO</p>

  <div class="person">
    <p class="person__name">Samira Haddadin</p>
    <p class="person__role">Fashion Designer</p>
  </div>

  <span class="divider"></span>

  <ul class="contact">
    <li>
      <svg viewBox="0 0 16 16" aria-hidden="true"><rect x="1" y="5" width="14" height="9" rx="2"/><rect x="3" y="2" width="10" height="4" rx="2"/></svg>
      +971 4 555 0192
    </li>
    <li>
      <svg viewBox="0 0 16 16" aria-hidden="true"><path d="M4 1l3 3-2 2c1 2 3 4 5 5l2-2 3 3-2 3C7 14 2 9 1 3z"/></svg>
      +971 50 555 0147
    </li>
    <li>
      <svg viewBox="0 0 16 16" aria-hidden="true"><circle cx="8" cy="8" r="7"/></svg>
      www.gravetto-example.com
    </li>
    <li>
      <svg viewBox="0 0 16 16" aria-hidden="true"><rect x="1" y="3" width="14" height="10" rx="1.5"/></svg>
      info@gravetto-example.com
    </li>
  </ul>
</section>

</body>
</html>
```